Graphics Design of Physics Book

Hi
Size : 8" x 11.25"
We are education book Publication Company and would like to have book cover for "Physics" it has 4 volumes. All 4 having the same color scheme and design except the volume no.
Blue is my personal favorite but u can use any color. Want to have a band at the bottom of the cover to place our Logo “VORNA Education” a PDF of the same is attached, or you can place logo anywhere according to ur design.
I need “Physics” as title of the book to be visible prominently.
And volume and volume no. should also be Visible and eye catching I prefer a Graphic to enhance the Volume No.
A background pattern can also be a option (it should be vector form so that color can be change later)
Please do not offer any cut and paste design I need very professional presentation.
Volume and Number can be in metallic 3D (CMYK) effect.
only Professional presentation will get feedback.
I have provided a sample artwork for reference do not follow it but can be a reference what I needed !

Target Market(s)

Students Class 9th to 12th

Industry/Entity Type

Education

Font styles to use
Serif

Colors
3176b5
0555a3
85abd2
cadf82
abd036
9bcb3c

Requirements
Must have
• Eye catching.
• “Physics” as title of the book to be visible prominently.
• volume and volume no. should also be Visible and eye catching
• I prefer a Graphic to enhance the Volume No.
• Icons for
• 1. Questions and answers
• 2. Theory Notes
• 3. Tips & Tricks
• 4. Previous Year's Reference Questions
• 5. Covers Complete Syllabus
Nice to have
• decent seamless background or metallic 3d effect (not to be print in special Ink) design should only be in CMYK.
Should not have
• Physics related Pictures or Icons (Specially E=mc2) or any scientist photograph or I Need pure graphic design

```html
<!DOCTYPE html>
<html lang="en">
<head>
<meta charset="utf-8">
<title>Physics Volume 1 — Book Cover</title>
<link rel="stylesheet" href="https://fonts.googleapis.com/css2?family=Arvo&family=Archivo+Black&family=Oswald:wght@500&display=swap">
<style>
  :root {
    --indigo: #2b1e78;
    --indigo-deep: #24196a;
    --ocean: #0a74ba;
    --sky: #8fb4dc;
    --light: #eef4fb;
    --gold: #f5c400;
    --ink: #11141f;
    --band-text: #1c1c2a;
    --white: #ffffff;
  }
  html, body {
    margin: 0;
    padding: 0;
    width: 854px;
    height: 1200px;
    overflow: hidden;
    background: var(--white);
  }
  .cover { display: block; width: 854px; height: 1200px; }
  .title { font-family: "Arvo", Georgia, serif; fill: var(--gold); }
  .volume-word { font-family: "Archivo Black", Arial, sans-serif; }
  .feature { font-family: "Oswald", "Arial Narrow", sans-serif; font-weight: 500; fill: var(--band-text); font-size: 21px; }
  .feature-dot { fill: var(--gold); }
  .publisher-name { font-family: "Archivo Black", Arial, sans-serif; fill: var(--ink); }
  .number-face { fill: var(--gold); }
  .number-depth { fill: var(--ink); }
  .divider-line { stroke: var(--ink); stroke-width: 3; }
</style>
</head>
<body>
<svg class="cover" viewBox="0 0 1067 1500" xmlns="http://www.w3.org/2000/svg" xmlns:xlink="http://www.w3.org/1999/xlink">
  <defs>
    <linearGradient id="bg-base" x1="0" y1="0" x2="1" y2="1">
      <stop offset="0" stop-color="var(--indigo)"/>
      <stop offset="0.45" stop-color="var(--indigo-deep)"/>
      <stop offset="0.75" stop-color="var(--ocean)"/>
      <stop offset="1" stop-color="var(--sky)"/>
    </linearGradient>
    <linearGradient id="bg-right" x1="0" y1="0" x2="1" y2="0">
      <stop offset="0.5" stop-color="#0a74ba" stop-opacity="0"/>
      <stop offset="1" stop-color="#0a74ba" stop-opacity="0.85"/>
    </linearGradient>
    <radialGradient id="bg-glow" cx="430" cy="1190" r="620" gradientUnits="userSpaceOnUse">
      <stop offset="0" stop-color="#ffffff"/>
      <stop offset="0.25" stop-color="#d8e6f5"/>
      <stop offset="0.6" stop-color="#5f93cc" stop-opacity="0.7"/>
      <stop offset="1" stop-color="#3a5fb0" stop-opacity="0"/>
    </radialGradient>
    <linearGradient id="metal" x1="0" y1="0" x2="1" y2="0">
      <stop offset="0" stop-color="#f4f4f6"/>
      <stop offset="0.35" stop-color="#8d9096"/>
      <stop offset="0.6" stop-color="#e9e9ee"/>
      <stop offset="1" stop-color="#7c7f86"/>
    </linearGradient>
    <linearGradient id="band" x1="0" y1="0" x2="0" y2="1">
      <stop offset="0" stop-color="#8c8d92"/>
      <stop offset="0.25" stop-color="#f3f3f5"/>
      <stop offset="0.7" stop-color="#ffffff"/>
      <stop offset="1" stop-color="#9a9ba0"/>
    </linearGradient>
    <path id="numeral-one" d="M437,585 L437,440 Q535,430 562,322 L792,322 L792,930 L898,930 L898,1108 L437,1108 L437,930 L545,930 L545,585 Z"/>
    <text id="volume-text" class="volume-word" transform="translate(305,1130) rotate(-90)" font-size="172" textLength="780" lengthAdjust="spacingAndGlyphs">VOLUME</text>
  </defs>

  <!-- Background -->
  <rect width="1067" height="1500" fill="url(#bg-base)"/>
  <rect width="1067" height="1500" fill="url(#bg-right)"/>
  <rect width="1067" height="1500" fill="url(#bg-glow)"/>

  <!-- Diagonal divider -->
  <line class="divider-line" x1="258" y1="0" x2="505" y2="935"/>
  <line class="divider-line" x1="565" y1="1180" x2="600" y2="1365" stroke-opacity="0.6"/>

  <!-- Title -->
  <text class="title" x="68" y="255" font-size="232" textLength="928" lengthAdjust="spacingAndGlyphs">PHYSICS</text>

  <!-- Volume word with depth -->
  <g class="volume">
    <g fill="var(--ink)">
      <use xlink:href="#volume-text" x="6" y="9"/>
      <use xlink:href="#volume-text" x="12" y="18"/>
      <use xlink:href="#volume-text" x="18" y="27"/>
      <use xlink:href="#volume-text" x="24" y="36"/>
      <use xlink:href="#volume-text" x="30" y="45"/>
    </g>
    <use xlink:href="#volume-text" fill="url(#metal)"/>
  </g>

  <!-- Volume number with depth -->
  <g class="volume-number">
    <g class="number-depth">
      <use xlink:href="#numeral-one" x="8" y="12"/>
      <use xlink:href="#numeral-one" x="16" y="24"/>
      <use xlink:href="#numeral-one" x="24" y="36"/>
      <use xlink:href="#numeral-one" x="32" y="48"/>
      <use xlink:href="#numeral-one" x="40" y="60"/>
      <use xlink:href="#numeral-one" x="48" y="71"/>
      <use xlink:href="#numeral-one" x="52" y="77"/>
    </g>
    <use class="number-face" xlink:href="#numeral-one"/>
  </g>

  <!-- Publisher -->
  <g class="publisher">
    <rect x="378" y="1233" width="307" height="99" fill="var(--white)"/>
    <text class="publisher-name" x="531" y="1296" font-size="32" text-anchor="middle" textLength="270" lengthAdjust="spacingAndGlyphs">VORNA Education</text>
  </g>

  <!-- Feature band -->
  <g class="feature-band">
    <rect x="0" y="1365" width="1067" height="63" fill="url(#band)"/>
    <circle class="feature-dot" cx="42" cy="1396" r="10"/>
    <text class="feature" x="60" y="1403" textLength="170" lengthAdjust="spacingAndGlyphs">Questions and answers</text>
    <circle class="feature-dot" cx="250" cy="1396" r="10"/>
    <text class="feature" x="268" y="1403" textLength="98" lengthAdjust="spacingAndGlyphs">Theory Notes</text>
    <circle class="feature-dot" cx="385" cy="1396" r="10"/>
    <text class="feature" x="403" y="1403" textLength="100" lengthAdjust="spacingAndGlyphs">Tips &amp; Tricks</text>
    <circle class="feature-dot" cx="523" cy="1396" r="10"/>
    <text class="feature" x="541" y="1403" textLength="265" lengthAdjust="spacingAndGlyphs">Previous Year's Reference Questions</text>
    <circle class="feature-dot" cx="826" cy="1396" r="10"/>
    <text class="feature" x="844" y="1403" textLength="190" lengthAdjust="spacingAndGlyphs">Covers Complete Syllabus</text>
  </g>
</svg>
</body>
</html>
```